Harbourline Electrical Solutions

On one side. LOGO (underneath:) Commercial Industrial Residential

- NAME & CONTACT DETAILS

Marcus T. Hollings
Project Manager

(Cell icon) (441) 555-0187
(Email icon) hlelectricalsolutions@mailvento.com
(Facebook & Instagram icons )@hlelectricalsolutions

Other side: LOGO - underneath ELECTRICAL CONSTRUCTION & MAINTENANCE . LED LIGHTING & AUTOMATION . LIFE SAFETY SYSTEMS (FIRE ALARM / SECURITY) . DATA & COMMUNICATION

```html
<!DOCTYPE html>
<html lang="en">
<head>
<meta charset="utf-8">
<title>Harbourline Electrical Solutions – Business Card</title>
<link href="https://fonts.googleapis.com/css2?family=Montserrat:wght@500;600&family=Roboto:wght@400&family=Saira+Semi+Condensed:wght@700&display=swap" rel="stylesheet">
<style>
  :root{
    --teal:#0d5a79;
    --slate:#3c4246;
    --ink:#333a3e;
    --paper:#ffffff;
    --backdrop:#2e2f31;
  }
  *{margin:0;padding:0;box-sizing:border-box}
  html,body{width:799px;height:1200px;overflow:hidden;background:var(--backdrop)}
  .stage{position:relative;width:799px;height:1200px}
  .card{position:absolute;left:60px;width:680px;height:388px;background:var(--paper);overflow:hidden;
        box-shadow:0 10px 26px rgba(0,0,0,.45)}
  .card--front{top:150px}
  .card--back{top:662px}

  .brand{position:absolute;display:flex;align-items:center;gap:16px}
  .brand__mark{width:46px;height:46px;background:var(--teal)}
  .brand__name{font-family:"Montserrat",sans-serif;font-weight:600;color:var(--teal);
        font-size:24px;line-height:1.12;letter-spacing:.14em;text-transform:uppercase}

  .card--front .brand{left:150px;top:34px}
  .sectors{position:absolute;font-family:"Montserrat",sans-serif;font-weight:500;
        font-size:15px;letter-spacing:.12em;text-transform:uppercase}
  .card--front .sectors{left:150px;top:140px;color:var(--teal)}

  .services-band{position:absolute;left:0;top:178px;width:100%;height:140px;background:var(--teal);
        color:#fff;font-family:"Roboto",sans-serif;padding:20px 44px 0}
  .services-band p{font-size:16px;line-height:1.5}
  .services-band .handle{margin-top:22px;padding-left:150px;font-size:16px}

  .card--back .brand{left:230px;top:52px}
  .person{position:absolute;left:48px;top:180px}
  .person__name{font-family:"Saira Semi Condensed",sans-serif;font-weight:700;color:var(--teal);font-size:26px;line-height:1}
  .person__role{font-family:"Roboto",sans-serif;color:var(--ink);font-size:14px;margin-top:4px}

  .contacts{position:absolute;left:330px;top:212px;list-style:none;font-family:"Roboto",sans-serif;
        color:var(--ink);font-size:15px}
  .contacts li{display:flex;align-items:center;gap:10px;height:23px}
  .contacts svg{width:16px;height:16px;flex:none}
  .contacts .no-icon{padding-left:26px}

  .footer-band{position:absolute;left:0;top:318px;width:680px;height:70px}
  .footer-band .sectors{left:250px;top:30px;color:#fff}
</style>
</head>
<body>
<main class="stage">

  <section class="card card--front" aria-label="Card front">
    <div class="brand">
      <span class="brand__mark"></span>
      <span class="brand__name">Harbourline<br>Electrical<br>Solutions</span>
    </div>
    <p class="sectors">Commercial &nbsp;|&nbsp; Industrial &nbsp;|&nbsp; Residential</p>
    <div class="services-band">
      <p>Electrical Construction &amp; Maintenance &nbsp;|&nbsp; Led Lighting &amp; Automation</p>
      <p>Life Safety Systems (Fire Alarm/Security) &nbsp;|&nbsp; Data &amp; Communication</p>
      <p class="handle">@hlelectricalsolutions</p>
    </div>
  </section>

  <section class="card card--back" aria-label="Card back">
    <div class="brand">
      <span class="brand__mark"></span>
      <span class="brand__name">Harbourline<br>Electrical<br>Solutions</span>
    </div>
    <div class="person">
      <p class="person__name">Marcus T. Hollings</p>
      <p class="person__role">Project Manager</p>
    </div>
    <ul class="contacts">
      <li>
        <svg viewBox="0 0 16 16" aria-hidden="true"><path fill="#333a3e" d="M3 3c1-1 2-1 3 0l1 2c0 1-1 1-1 2 1 2 2 3 4 4 1 0 1-1 2-1l2 1c1 1 1 2 0 3-1 1-3 1-5 0C6 13 4 11 2 8 1 6 2 4 3 3z"/></svg>
        (441) 555-0187
      </li>
      <li>
        <svg viewBox="0 0 16 16" aria-hidden="true"><rect x="1" y="3" width="14" height="10" fill="#333a3e"/><path d="M1 3l7 6 7-6" fill="none" stroke="#fff" stroke-width="1.4"/></svg>
        hlelectricalsolutions@mailvento.com
      </li>
      <li class="no-icon">@hlelectricalsolutions</li>
    </ul>
    <svg class="footer-band" viewBox="0 0 680 70" aria-hidden="true">
      <rect x="0" y="0" width="260" height="14" fill="var(--slate)"/>
      <path d="M200 14 Q210 0 232 0 H680 V70 H200 Z" fill="var(--teal)"/>
      <rect x="0" y="14" width="200" height="56" fill="var(--paper)"/>
    </svg>
    <div class="footer-band" style="pointer-events:none">
      <p class="sectors">Commercial &nbsp;|&nbsp; Industrial &nbsp;|&nbsp; Residential</p>
    </div>
  </section>

</main>
</body>
</html>
```